Specialised investor in e-mobility and energy wants business card design

We need a business card design that fits our existing corporate design. <The look and feel must be 'sharp'/'clean', dynamic, communicate momentum, professionalism etc (as one would imagine from a firm in the financial sector). We like the idea of a reverse-side of the card that includes the logo, and the name and contact details on the other. We expect the deliverable to be whatever format might be required to be able to get cards printed directly by a service such as kelmo press. Our website is www.zub.capital

```html
<!DOCTYPE html>
<html lang="en">
<head>
<meta charset="utf-8">
<title>ZUB Capital – Business Card</title>
<link href="https://fonts.googleapis.com/css2?family=Questrial&family=Arimo:wght@400;700&display=swap" rel="stylesheet">
<style>
  :root {
    --page-bg: #e9eaec;
    --brand-green: #88b34b;
    --deep-green: #2f5320;
    --accent-green: #86b83c;
    --ink: #111111;
    --card-white: #ffffff;
  }
  * { box-sizing: border-box; margin: 0; padding: 0; }
  html, body { width: 1200px; height: 900px; overflow: hidden; }
  body {
    background: var(--page-bg);
    display: flex;
    flex-direction: column;
    align-items: center;
    justify-content: center;
    gap: 44px;
    font-family: "Arimo", Arial, sans-serif;
  }
  .card {
    width: 680px;
    height: 400px;
    position: relative;
    box-shadow: 0 6px 18px rgba(0,0,0,0.12);
  }
  .card--front {
    background: var(--brand-green);
    display: flex;
    align-items: center;
    justify-content: center;
  }
  .card--back {
    background: var(--card-white);
    display: flex;
    align-items: center;
    justify-content: space-between;
    padding: 0 44px 0 56px;
  }
  .wordmark {
    font-family: "Questrial", "Century Gothic", sans-serif;
    color: var(--deep-green);
    font-weight: 400;
    letter-spacing: 1px;
    white-space: nowrap;
  }
  .wordmark--large { font-size: 84px; }
  .wordmark--small { font-size: 46px; }
  .contact-block {
    font-size: 15px;
    line-height: 1.22;
    color: var(--ink);
    width: 270px;
  }
  .contact-block__intro { margin-bottom: 2px; }
  .person__name {
    color: var(--accent-green);
    font-weight: 700;
    text-transform: uppercase;
    letter-spacing: 0.2px;
  }
  .contact-line {
    display: flex;
    align-items: center;
    gap: 8px;
    padding-left: 4px;
  }
  .contact-line svg { width: 12px; height: 12px; flex: none; fill: var(--deep-green); }
  .company-address { margin-top: 2px; }
</style>
</head>
<body>

  <section class="card card--front" aria-label="Card front">
    <span class="wordmark wordmark--large">ZUB capital</span>
  </section>

  <section class="card card--back" aria-label="Card back">
    <span class="wordmark wordmark--small">ZUB capital</span>

    <div class="contact-block">
      <p class="contact-block__intro">Or contact the team directly</p>

      <p class="person__name">Peter Oakhurst</p>
      <p class="contact-line">
        <svg viewBox="0 0 12 12" aria-hidden="true"><path d="M1 3c0-1 1-2 2-2h6c1 0 2 1 2 2v1H8V3H4v1H1zM2 5h8l1 6H1z"/></svg>
        +41 79555 0148
      </p>
      <p class="contact-line">
        <svg viewBox="0 0 12 12" aria-hidden="true"><path d="M0 2h12v8H0zM1 3v.5l5 3.2 5-3.2V3z" fill-rule="evenodd"/></svg>
        peter@zub.capital
      </p>
      <p class="contact-line">
        <svg viewBox="0 0 12 12" aria-hidden="true"><circle cx="6" cy="6" r="5.5"/></svg>
        www.zub.capital
      </p>

      <p class="person__name">Kenji Arata</p>
      <p class="contact-line">
        <svg viewBox="0 0 12 12" aria-hidden="true"><path d="M0 2h12v8H0zM1 3v.5l5 3.2 5-3.2V3z" fill-rule="evenodd"/></svg>
        kenji@zub.capital
      </p>

      <p class="person__name">Daniel Ferrow</p>
      <p class="contact-line">
        <svg viewBox="0 0 12 12" aria-hidden="true"><path d="M0 2h12v8H0zM1 3v.5l5 3.2 5-3.2V3z" fill-rule="evenodd"/></svg>
        daniel@zub.capital
      </p>

      <p class="person__name">Clara Winslow</p>
      <p class="contact-line">
        <svg viewBox="0 0 12 12" aria-hidden="true"><path d="M0 2h12v8H0zM1 3v.5l5 3.2 5-3.2V3z" fill-rule="evenodd"/></svg>
        clara@zub.capital
      </p>

      <p class="company-address">ZUB Capital S.A.<br>Geneva, Switzerland</p>
    </div>
  </section>

</body>
</html>
```